IT Company needs full suite of stationery

Our company 4627 Vantor Holdings Inc. is an IT company based in Toronto, Canada. Based on our logo we would like to see business cards(front and back), letterhead, envelope, brochure template. Design would be simple, not too bright, modern but can be used for many years, good theme throughout. Our official logo is the the fullcolor_a, full company name is 4627 Vantor Holdings Inc., Please include full company name on all pieces. Logo can be modified to be the graphic only with the "4627 Holdings", I have cropped it myself for a couple files but I am no designer. We will provide lots of feedback so post early and often.

Project Deadline Extended
Reason: Very busy around the holidays, like a lot of the designs currently submitted, will definitely be picking one. Thanks for your submissions and merry Christmas and Happy New Year to everyone.

Industry/Entity Type

Business

```html
<!DOCTYPE html>
<html lang="en">
<head>
<meta charset="utf-8">
<title>4627 Vantor Holdings Inc. — Stationery Suite</title>
<link href="https://fonts.googleapis.com/css2?family=Exo+2:wght@500;600&display=swap" rel="stylesheet">
<style>
  :root{
    --backdrop:#e9eaeb;
    --paper:#ffffff;
    --green:#4f9e45;
    --green-light:#8cc152;
    --green-dark:#3b8a3c;
    --ink:#4a4b4d;
    --ink-soft:#6d6e70;
    --name-blue:#2f4f8f;
  }
  *{margin:0;padding:0;box-sizing:border-box}
  html,body{width:1200px;height:937px;overflow:hidden}
  body{background:var(--backdrop);font-family:"Exo 2",sans-serif;color:var(--ink);position:relative}
  .piece{position:absolute;background:var(--paper);overflow:hidden}

  .band{position:absolute;left:0;right:0;bottom:0;
    background:linear-gradient(180deg,rgba(140,193,82,0) 0%,rgba(140,193,82,.55) 35%,var(--green) 75%,var(--green-dark) 100%)}

  .brand{position:absolute;display:flex;align-items:center;font-weight:600;color:var(--ink);white-space:nowrap}
  .brand-dot{border-radius:50%;background:var(--green);flex:none}
  .brand-name{line-height:1}

  /* Letterhead */
  .letterhead{left:184px;top:68px;width:386px;height:544px}
  .letterhead .brand{left:20px;top:28px;font-size:17px;gap:8px}
  .letterhead .brand-dot{width:30px;height:30px}
  .letterhead .contact{position:absolute;right:18px;top:22px;text-align:right;font-style:normal;font-size:5.5px;line-height:8px;color:var(--ink-soft)}
  .letterhead .band{height:125px}

  /* Folder */
  .folder{left:635px;top:40px;width:459px;height:576px}
  .folder .brand{left:0;right:0;justify-content:center;top:250px;font-size:30px;gap:12px}
  .folder .brand-dot{width:60px;height:60px}
  .folder .band{height:140px}

  /* Business card front */
  .card-front{left:45px;top:658px;width:177px;height:100px}
  .card-front .brand{left:8px;top:12px;font-size:9.5px;gap:5px}
  .card-front .brand-dot{width:18px;height:18px}
  .card-front .person{position:absolute;right:8px;top:10px;text-align:right}
  .card-front .person-name{font-size:6px;color:var(--name-blue);letter-spacing:.3px;text-transform:uppercase}
  .card-front .person-role{font-size:4.5px;color:var(--ink-soft);text-transform:uppercase}
  .card-front .card-contact{position:absolute;right:8px;top:34px;text-align:right;font-size:3.6px;line-height:5px;color:var(--ink-soft)}
  .card-front .band{height:40px}

  /* Business card back */
  .card-back{left:45px;top:785px;width:177px;height:100px}
  .card-back .brand{right:10px;top:16px;font-size:9px;gap:5px}
  .card-back .brand-dot{width:18px;height:18px}
  .card-back .band{height:46px}

  /* Envelope front */
  .envelope{left:264px;top:671px;width:433px;height:214px}
  .envelope .brand{left:18px;top:24px;font-size:16px;gap:7px}
  .envelope .brand-dot{width:28px;height:28px}
  .envelope .band{height:110px}

  /* Envelope back */
  .envelope-back{left:737px;top:671px;width:432px;height:208px}
  .envelope-back .flap{position:absolute;left:0;top:0;width:100%;height:73px;border-radius:0 0 42px 42px;background:linear-gradient(90deg,var(--green-dark),var(--green-light) 50%,var(--green-dark))}
  .envelope-back .site{position:absolute;left:0;right:0;top:28px;text-align:center;color:#fff;font-size:13px;font-weight:500;letter-spacing:2px}
</style>
</head>
<body>

<section class="piece letterhead" aria-label="Letterhead">
  <div class="brand"><span class="brand-dot"></span><span class="brand-name">4627 Holdings</span></div>
  <address class="contact">
    4627 Vantor Holdings Inc.<br>
    88 Front Street West, Toronto ON<br>
    416 555 0182<br>
    info@vantor4627.ca
  </address>
  <div class="band" role="img" aria-label="Green decorative wave band"></div>
</section>

<section class="piece folder" aria-label="Presentation folder">
  <div class="brand"><span class="brand-dot"></span><span class="brand-name">4627 Holdings</span></div>
  <div class="band" role="img" aria-label="Green decorative wave band"></div>
</section>

<section class="piece card-front" aria-label="Business card front">
  <div class="brand"><span class="brand-dot"></span><span class="brand-name">4627 Holdings</span></div>
  <div class="person">
    <div class="person-name">Dana Keller</div>
    <div class="person-role">President</div>
  </div>
  <div class="card-contact">
    4627 Vantor Holdings Inc.<br>
    88 Front St W, Toronto<br>
    416 555 0182<br>
    info@vantor4627.ca<br>
    www.vantor4627.ca
  </div>
  <div class="band" role="img" aria-label="Green decorative wave band"></div>
</section>

<section class="piece card-back" aria-label="Business card back">
  <div class="brand"><span class="brand-dot"></span><span class="brand-name">4627 Holdings</span></div>
  <div class="band" role="img" aria-label="Green decorative wave band"></div>
</section>

<section class="piece envelope" aria-label="Envelope front">
  <div class="brand"><span class="brand-dot"></span><span class="brand-name">4627 Holdings</span></div>
  <div class="band" role="img" aria-label="Green decorative wave band"></div>
</section>

<section class="piece envelope-back" aria-label="Envelope back">
  <div class="flap"></div>
  <div class="site">www.vantor4627.ca</div>
</section>

</body>
</html>
```